Business Card for a Jewellery Brand

Business card for an upscale jewellery brand. Attached is the brand logo and icon and color board. I am looking for two card versions: one for the founder and one is generic. The card should be elegant and convey upscale and premium feel. I am open to both square and rectangle card shapes.

Industry/Entity Type

Jewelry

Contact Information for Business Card

Two cards: (1) Sunela Parvaniya (Founder) (2) General
(1) Sunela Parvaniya card should have Name: Sunela Parvaniya, Title: Founder Email id: sunela@quiremo.com.au. Phone no: +61452913307
(2) Generic card should have Email id: info@quiremo.com.au. Phone no: +61436207518

Requirements
Must have
• Workmark
• ICON
• Phone no
• Email ID
• ABN: 58219740312 (Note: ABN is Business number in Australia)
• Website: www.quiremo.com.au
• Instagram: quiremo_jewellery
• Facebook: @quiremojewellery
Nice to have
• Tagline

```html
<!DOCTYPE html>
<html lang="en">
<head>
<meta charset="utf-8">
<title>Quiremo Business Cards</title>
<link rel="stylesheet" href="https://fonts.googleapis.com/css2?family=Montserrat:wght@400;500;600&family=Open+Sans:wght@400;600&display=swap">
<style>
  :root {
    --backdrop: #a8a8a8;
    --card-white: #ffffff;
    --blush: #e69a96;
    --ink: #1e1e1e;
    --paper-text: #ffffff;
  }
  * { margin: 0; padding: 0; box-sizing: border-box; }
  html, body {
    width: 1200px;
    height: 900px;
    overflow: hidden;
    background: var(--backdrop);
  }
  .canvas {
    position: relative;
    width: 1200px;
    height: 900px;
  }
  .card {
    position: absolute;
    top: 238px;
    width: 400px;
    height: 400px;
  }
  .card--founder { left: 192px; background: var(--card-white); }
  .card--brand { left: 636px; background: var(--blush); }

  .founder-name {
    position: absolute;
    left: 26px;
    top: 36px;
    font-family: "Montserrat", sans-serif;
    font-weight: 600;
    font-size: 22px;
    letter-spacing: 1.4px;
    color: var(--blush);
    text-transform: uppercase;
    white-space: nowrap;
  }
  .founder-title {
    position: absolute;
    left: 26px;
    top: 66px;
    font-family: "Open Sans", sans-serif;
    font-size: 17px;
    color: var(--ink);
  }
  .abn {
    position: absolute;
    left: 25px;
    top: 106px;
    font-family: "Open Sans", sans-serif;
    font-size: 16px;
    color: var(--ink);
  }
  .abn-label { color: var(--blush); font-weight: 600; }

  .brand-mark {
    position: absolute;
    left: 238px;
    top: 128px;
    width: 56px;
    height: 56px;
    border-radius: 50%;
    background: var(--blush);
  }

  .wordmark {
    position: absolute;
    font-family: "Montserrat", sans-serif;
    font-weight: 500;
    text-transform: uppercase;
    white-space: nowrap;
  }
  .wordmark--founder {
    right: 44px;
    top: 228px;
    font-size: 30px;
    letter-spacing: 5px;
    color: var(--blush);
  }
  .wordmark--brand {
    left: 0;
    width: 400px;
    top: 126px;
    text-align: center;
    font-size: 50px;
    letter-spacing: 8px;
    padding-left: 8px;
    color: var(--paper-text);
  }

  .contact-list {
    position: absolute;
    left: 25px;
    top: 285px;
    list-style: none;
    font-family: "Open Sans", sans-serif;
    font-size: 16px;
    color: var(--ink);
  }
  .contact-list li {
    display: flex;
    align-items: center;
    height: 23.5px;
  }
  .contact-icon {
    width: 12px;
    height: 12px;
    margin-right: 7px;
    fill: var(--blush);
  }

  .social-row {
    position: absolute;
    left: 40px;
    top: 264px;
    width: 321px;
    height: 24px;
  }
  .social-rule {
    position: absolute;
    top: 11.5px;
    height: 1px;
    background: var(--paper-text);
  }
  .social-rule--left { left: 0; width: 114px; }
  .social-rule--right { right: 0; width: 125px; }
  .social-dot {
    position: absolute;
    top: 0;
    width: 24px;
    height: 24px;
    border-radius: 50%;
    background: var(--paper-text);
  }
  .social-dot--one { left: 126px; }
  .social-dot--two { left: 161px; }
  .social-handle {
    position: absolute;
    left: 0;
    width: 400px;
    top: 299px;
    text-align: center;
    font-family: "Open Sans", sans-serif;
    font-size: 16px;
    color: var(--paper-text);
  }
</style>
</head>
<body>
<main class="canvas">
  <section class="card card--founder" aria-label="Founder card">
    <h1 class="founder-name">Sunela Parvaniya</h1>
    <p class="founder-title">Founder</p>
    <p class="abn"><span class="abn-label">ABN:</span> 58219740312</p>
    <span class="brand-mark" role="img" aria-label="Brand icon"></span>
    <p class="wordmark wordmark--founder">Quiremo</p>
    <ul class="contact-list">
      <li>
        <svg class="contact-icon" viewBox="0 0 12 12" aria-hidden="true"><path d="M2.4 0.5 L4.3 2.6 L3.4 4 Q4.6 6.8 7.9 8.6 L9.3 7.7 L11.5 9.6 L10.2 11.4 Q5.5 11 2.3 6.6 Q0.6 3.9 0.9 1.7 Z"/></svg>
        +61452913307
      </li>
      <li>
        <svg class="contact-icon" viewBox="0 0 12 12" aria-hidden="true"><path d="M0.5 2.5 H11.5 V3.2 L6 6.6 L0.5 3.2 Z M0.5 4.4 L6 7.8 L11.5 4.4 V9.5 H0.5 Z"/></svg>
        sunela@quiremo.com.au
      </li>
      <li>
        <svg class="contact-icon" viewBox="0 0 12 12" aria-hidden="true"><circle cx="6" cy="6" r="5.5"/></svg>
        www.quiremo.com.au
      </li>
    </ul>
  </section>

  <section class="card card--brand" aria-label="Brand card">
    <p class="wordmark wordmark--brand">Quiremo</p>
    <div class="social-row" aria-hidden="true">
      <span class="social-rule social-rule--left"></span>
      <span class="social-dot social-dot--one"></span>
      <span class="social-dot social-dot--two"></span>
      <span class="social-rule social-rule--right"></span>
    </div>
    <p class="social-handle">@quiremojewellery</p>
  </section>
</main>
</body>
</html>
```